design a construction company business card

Design business card around our logo. Card must have all the typical info: name, title, address, phone, email, business name, etc. Somewhere on the card I would like to see our motto "Solid Foundations... Driven by Craft." Consider adding a splash of bright orange to the card to complement the blues and silvers/grays in the logo. We are open to metallic inks, textures, etc. We would like to see options on both light and dark backgrounds. The font in the logo is Euro Technic Extended Regular.

```html
<!DOCTYPE html>
<html lang="en">
<head>
<meta charset="utf-8">
<title>Harlow Building, Inc – Business Card</title>
<link rel="stylesheet" href="https://fonts.googleapis.com/css2?family=Exo+2:wght@400;600&display=swap">
<style>
  :root {
    --bg: #8f8f8f;
    --card-dark: #0d0d0e;
    --card-mid: #1e1f22;
    --blue: #2f73d9;
    --blue-deep: #2a3fb0;
    --white: #f2f2f2;
    --grey-text: #8a8d93;
  }
  * { margin: 0; padding: 0; box-sizing: border-box; }
  html, body { width: 1200px; height: 900px; overflow: hidden; }
  body {
    background: var(--bg);
    font-family: "Exo 2", "Open Sans", sans-serif;
    position: relative;
  }
  .card {
    position: absolute;
    width: 560px;
    height: 320px;
    border-radius: 3px;
    background: radial-gradient(ellipse at 55% 40%, var(--card-mid) 0%, var(--card-dark) 75%);
    box-shadow: 0 10px 22px rgba(0,0,0,.3);
    overflow: hidden;
    color: var(--white);
  }
  /* back side: brand name, rule and motto */
  .card--back { left: 580px; top: 90px; }
  .back__brand {
    position: absolute; left: 0; right: 0; top: 118px;
    text-align: center;
    font-size: 32px; font-weight: 600; letter-spacing: 2px;
    color: var(--blue);
  }
  .back__rule {
    position: absolute; left: 40px; right: 40px; top: 178px;
    height: 4px; background: var(--blue-deep);
  }
  .back__motto {
    position: absolute; left: 0; right: 0; top: 196px;
    text-align: center;
    font-size: 15px; letter-spacing: .5px;
    color: var(--grey-text);
  }
  /* front side: contact details */
  .card--front { left: 60px; top: 440px; }
  .front__tab {
    position: absolute; left: 0; top: 22px;
    width: 12px; height: 24px;
    background: var(--blue); border-radius: 0 3px 3px 0;
  }
  .front__name {
    position: absolute; left: 50px; top: 20px;
    font-size: 22px; font-weight: 600; color: var(--blue);
  }
  .front__name span { font-weight: 400; }
  .front__title {
    position: absolute; left: 50px; top: 50px;
    font-size: 15px; color: var(--white);
  }
  .front__title span { color: var(--blue); }
  .contact {
    position: absolute; left: 22px; top: 92px;
    list-style: none; font-size: 15px; line-height: 25px;
  }
  .contact li { display: flex; align-items: center; gap: 10px; }
  .contact .icon {
    width: 18px; height: 18px; border-radius: 50%;
    background: var(--blue);
    display: inline-flex; align-items: center; justify-content: center;
    flex: none;
  }
  .contact .icon svg { width: 11px; height: 11px; }
  .front__brand {
    position: absolute; right: 34px; top: 104px;
    display: flex; align-items: flex-start; gap: 10px;
    font-size: 24px; font-weight: 600; line-height: 28px;
    color: var(--blue); letter-spacing: 1px;
    text-align: right;
  }
  .front__brand .mark {
    width: 14px; height: 14px; margin-top: 7px;
    background: var(--blue); flex: none;
  }
  .front__address {
    position: absolute; right: 34px; bottom: 30px;
    text-align: right; font-size: 15px; line-height: 22px;
    font-style: normal; color: var(--white);
  }
</style>
</head>
<body>

  <section class="card card--back" aria-label="Card back">
    <div class="back__brand">HARLOW BUILDING, INC.</div>
    <div class="back__rule"></div>
    <p class="back__motto">Solid Foundations... Driven by Craft</p>
  </section>

  <section class="card card--front" aria-label="Card front">
    <div class="front__tab"></div>
    <h1 class="front__name">DALE <span>marsh</span></h1>
    <p class="front__title">CEO of <span>Harlow Building, INC</span></p>

    <ul class="contact">
      <li>
        <span class="icon"><svg viewBox="0 0 12 12"><path d="M2.5 1 L4.5 1 L5 3.5 L3.8 4.4 Q4.8 6.8 7.6 8.2 L8.5 7 L11 7.5 L11 9.5 Q10.5 11 9 11 Q2 10 1 3 Q1 1.5 2.5 1Z" fill="#fff"/></svg></span>
        (02) 5550 1842
      </li>
      <li>
        <span class="icon"><svg viewBox="0 0 12 12"><rect x="3.5" y="1" width="5" height="10" rx="1" fill="none" stroke="#fff" stroke-width="1.2"/><circle cx="6" cy="9.3" r=".6" fill="#fff"/></svg></span>
        0400 555 271
      </li>
      <li>
        <span class="icon"><svg viewBox="0 0 12 12"><rect x="1.5" y="3" width="9" height="6.5" fill="none" stroke="#fff" stroke-width="1.1"/><path d="M1.5 3 L6 7 L10.5 3" fill="none" stroke="#fff" stroke-width="1.1"/></svg></span>
        info@harlowbuilding.com
      </li>
      <li>
        <span class="icon"><svg viewBox="0 0 12 12"><circle cx="6" cy="6" r="4.5" fill="none" stroke="#fff" stroke-width="1.1"/><path d="M1.5 6 H10.5 M6 1.5 Q3.5 6 6 10.5 M6 1.5 Q8.5 6 6 10.5" fill="none" stroke="#fff" stroke-width=".9"/></svg></span>
        www.harlowbuilding.com
      </li>
    </ul>

    <div class="front__brand"><span class="mark"></span><span>HARLOW<br>BUILDING, INC.</span></div>

    <address class="front__address">
      12/8 Mill Rd, Eastfield<br>NSW 2099
    </address>
  </section>

</body>
</html>
```